Infoblatt
Zielgruppe
Talentförderung, Personalentwicklung, Beratung von Personalabteilungen
Zielgruppe: Personaler, HR Verantwortliche
Aufgabenstellung
Es geht um einen "One-Pager", der auf einem Kongress ausgelegt werden soll und in Kurzform einen Überblick über unser Unternehmen und unser Angebot informieren soll.
Wir haben Visitenkarten auf Recyclingpapier und möchten das Blatt konsistent auf das gleiche Papier drucken lassen, daher einfarbig schwarz. Format DIN A4 Hoch.
IDEE: Vom Stil wie eine Infografik aufbauen
TYPO: unser LOGO ist BEBAS NEUE und unsere Schrift Helvetica

```html
<!DOCTYPE html>
<html lang="de">
<head>
<meta charset="utf-8">
<title>ZIELWERK – Infoblatt</title>
<link rel="stylesheet" href="https://fonts.googleapis.com/css2?family=Bebas+Neue&family=Arimo:ital,wght@0,400;0,700;1,400;1,700&display=swap">
<style>
  :root {
    --stage: #ecebe7;
    --paper: #ffffff;
    --ink: #1a1a1a;
    --mid-gray: #8f8f8f;
    --bar-gray: #9a9a9a;
    --light-bar: #dcdcdc;
    --soft-text: #8a8a8a;
  }
  * { margin: 0; padding: 0; box-sizing: border-box; }
  html, body {
    width: 900px; height: 1200px; overflow: hidden;
    background: var(--stage);
    font-family: "Arimo", Helvetica, Arial, sans-serif;
  }
  .sheet {
    position: absolute; left: 25px; top: 6px;
    width: 850px; height: 1189px;
    background: var(--paper); overflow: hidden;
  }
  .site-url {
    position: absolute; left: 25px; top: 22px;
    font-size: 11px; color: var(--soft-text);
  }
  .brand-name {
    position: absolute; left: 24px; top: 28px;
    font-family: "Bebas Neue", sans-serif; font-size: 124px; line-height: 1;
    color: var(--ink); letter-spacing: 1px;
  }
  .tagline {
    position: absolute; right: 29px; top: 143px;
    font-size: 23px; font-weight: 400; color: var(--soft-text);
  }
  .team-photo-area {
    position: absolute; left: 0; top: 369px; width: 850px; height: 820px;
    background:
      radial-gradient(ellipse 260px 300px at 260px 300px, #b9b9b9 0%, rgba(200,200,200,0.4) 55%, rgba(255,255,255,0) 100%),
      linear-gradient(180deg, #f4f4f4 0%, #e8e8e8 45%, #d9d9d9 70%, #c9c9c9 100%);
  }
  .workshop-photo-area {
    position: absolute; left: 0; top: 1000px; width: 850px; height: 189px;
    background: linear-gradient(180deg, #c8c8c8 0%, #dedede 45%, #b4b4b4 100%);
  }
  .intro-band {
    position: absolute; left: 29px; top: 173px; width: 794px; height: 196px;
    background: var(--ink);
  }
  .intro-text {
    position: absolute; left: 48px; top: 187px; width: 380px;
    color: #fff; font-weight: 700; font-style: italic;
    font-size: 22px; line-height: 30.5px;
  }
  .services {
    position: absolute; left: 49px; top: 348px; width: 286px; height: 141px;
    background: #fff; border: 1px solid #777;
    box-shadow: 3px 3px 5px rgba(0,0,0,0.35);
    font-size: 12px; line-height: 13.5px; color: var(--ink);
  }
  .services h3 {
    background: var(--bar-gray); color: #fff;
    font-size: 12.5px; font-weight: 700; text-align: center;
    margin: 2px 2px 0; padding: 2px 0 3px;
  }
  .services ul { list-style: none; padding: 4px 8px 4px 8px; }
  .frame-line { position: absolute; background: var(--ink); }
  .team-circles { position: absolute; left: 0; top: 0; }
  .values {
    position: absolute; right: 0; top: 525px; width: 520px;
    display: flex; flex-direction: column; align-items: flex-end; gap: 7.6px;
  }
  .values span {
    display: block; background: var(--light-bar);
    font-family: "Bebas Neue", sans-serif; font-size: 25px; line-height: 25px;
    letter-spacing: 2.2px; color: var(--ink);
    padding: 1px 50px 0 8px; height: 25px;
  }
  .glossary {
    position: absolute; left: 312px; top: 828px;
    font-size: 9.8px; line-height: 15px; font-style: italic; color: #333;
  }
  .glossary b { font-weight: 700; }
  .belief-band {
    position: absolute; left: -20px; top: 890px; width: 890px; height: 128px;
    background: linear-gradient(180deg, #9c9c9c 0%, #8a8a8a 100%);
    transform: rotate(-2deg);
    display: flex; align-items: center; justify-content: center;
  }
  .belief-band p {
    color: #fff; font-style: italic; font-size: 21px; line-height: 27px;
    text-align: center; letter-spacing: 0.4px;
  }
  .contact {
    position: absolute; right: 53px; top: 1062px; text-align: right;
    color: #fff; font-size: 15px; line-height: 21px;
    text-shadow: 0 0 3px rgba(0,0,0,0.25);
  }
  .contact .contact-name {
    font-family: "Bebas Neue", sans-serif; font-size: 21px; letter-spacing: 0.5px;
  }
  .contact .contact-mail { font-weight: 700; }
</style>
</head>
<body>
  <main class="sheet">
    <div class="team-photo-area" role="img" aria-label="Unscharfes Foto einer Gruppe von Kollegen im Gespräch"></div>
    <div class="workshop-photo-area" role="img" aria-label="Foto eines Flipcharts mit Notizen und Stiften"></div>

    <div class="site-url">www.zielwerk-beispiel.de</div>
    <h1 class="brand-name">ZIELWERK</h1>
    <div class="tagline">Vordenken und nachdenken</div>

    <div class="intro-band"></div>
    <p class="intro-text">Wir beraten Unternehmen im Rahmen der Talentförderung und helfen Jugendlichen auf dem Weg in ihr Berufsleben.</p>

    <section class="services">
      <h3>Für Unternehmen:</h3>
      <ul>
        <li>Talentförderung &amp; Talent Management</li>
        <li>Professionalisierung der Personalarbeit</li>
        <li>Organisationsentwicklung</li>
        <li>Potentialorientierte Mitarbeiterführung</li>
      </ul>
      <h3>Für die junge Generation:</h3>
      <ul>
        <li>Berufsorientierung</li>
        <li>Bewerbungscoaching</li>
      </ul>
    </section>

    <div class="frame-line" style="left:29px; top:470px; width:1px; height:397px;"></div>
    <div class="frame-line" style="left:834px; top:470px; width:1px; height:397px;"></div>
    <div class="frame-line" style="left:29px; top:867px; width:806px; height:1px;"></div>
    <div class="frame-line" style="left:29px; top:1016px; width:1px; height:141px;"></div>
    <div class="frame-line" style="left:834px; top:1016px; width:1px; height:141px;"></div>
    <div class="frame-line" style="left:29px; top:1157px; width:806px; height:1px;"></div>

    <svg class="team-circles" width="850" height="600" viewBox="0 0 850 600" aria-hidden="false">
      <defs>
        <radialGradient id="portraitFill" cx="50%" cy="45%" r="60%">
          <stop offset="0%" stop-color="#f2f2f2"/>
          <stop offset="100%" stop-color="#c4c4c4"/>
        </radialGradient>
      </defs>
      <g fill="rgba(0,0,0,0.22)">
        <circle cx="490" cy="286" r="71"/>
        <circle cx="636" cy="268" r="64"/>
        <circle cx="774" cy="277" r="69"/>
        <circle cx="472" cy="432" r="61"/>
        <circle cx="624" cy="437" r="93"/>
        <circle cx="788" cy="430" r="80"/>
      </g>
      <g fill="url(#portraitFill)" stroke="#1a1a1a" stroke-width="1.5">
        <circle cx="486" cy="282" r="70" role="img" aria-label="Porträt Teammitglied"/>
        <circle cx="632" cy="264" r="63" role="img" aria-label="Porträt Teammitglied"/>
        <circle cx="770" cy="273" r="68" role="img" aria-label="Porträt Teammitglied"/>
        <circle cx="468" cy="428" r="60" role="img" aria-label="Porträt Teammitglied"/>
        <circle cx="620" cy="433" r="92" role="img" aria-label="Porträt Teammitglied"/>
        <circle cx="784" cy="426" r="79" role="img" aria-label="Porträt Teammitglied"/>
      </g>
    </svg>

    <div class="values">
      <span>Wir legen grossen Wert</span>
      <span>auf eine Beziehung,</span>
      <span>die mandare, nicht kundare</span>
      <span>entspricht.</span>
      <span>Für uns ist der partnerschaftliche</span>
      <span>Umgang mit unseren Mandanten</span>
      <span>das Fundament.</span>
      <span>Wir haben keine Kunden.</span>
      <span>Wir unterstützen Mandanten.</span>
    </div>

    <p class="glossary">
      <b>Kundare</b> heißt marktschreierisch anpreisen, hinters Licht führen, täuschen.<br>
      <b>Mandare</b> heißt beauftragen, Vertrauen schenken.
    </p>

    <div class="belief-band">
      <p>Wir glauben, dass sich persönliche und ökonomische Werte ergänzen -<br>
      mehr noch, dass sie langfristig nicht ohne einander auskommen<br>
      und dass sich emotionale Bindung als Mehrwert in Zahlen ausdrückt.</p>
    </div>

    <address class="contact" style="font-style:normal;">
      <div class="contact-name">ZIELWERK,</div>
      <div>Lindenweg 12, 40210 Musterstadt,</div>
      <div>Fon: 0211.55501234,</div>
      <div class="contact-mail">info@zielwerk-beispiel.de</div>
    </address>
  </main>
</body>
</html>
```